Creation of brand identity and website "Tandem K"

I am currently seeking an brand, identity and web design for a new project called Tandem K. This is a brand new concept from scratch and you have free-reign on the whole design process, taking into account my preference below.

Must include the name "Tandem K", or "Tandem K: Or the year I woke Up". Kudos is this forms part of the brands logo

Design that can be easily scaled to potentially include: a blog, timeline and vlogs.

Minimal but effective use of colour (however any colours and combinations permitted

Use of icons/graphics over text wherever possible

Minimal use of frames and borders

I appreciate this is a fairly wide scope so please contact me on marblefinch@postwillow.com with any questions or more information on what the project is.

Target Market(s)

Male and Female 20-40
Blog readers
Selfhelp

Industry/Entity Type

Seeking

Number of Pages Required

1 page

Font styles to use
Serif
Sans Serif

Requirements
Must have
• It is in effect a blog design, so about me section, recent blog / archived posts, reader comments / Q and A section.
• A coded design would be appreciated to make my life easier however I have left the design as uncoded as getting the right design matters more to me and I want to keep the project open to as many designers as possible
Nice to have
• See project description for other details and please ask if you need anything else :)
Should not have
• Mustn't be cluttered or feel fussy
• Promote icons over text
• Frames / multiple borders

```html
<!DOCTYPE html>
<html lang="en">
<head>
<meta charset="utf-8">
<title>Tandem K: Or the year I woke Up</title>
<link href="https://fonts.googleapis.com/css2?family=Cinzel:wght@400;700&family=Open+Sans:wght@400;600;700&display=swap" rel="stylesheet">
<style>
:root{
  --green:#8db31e;
  --green-dark:#76991a;
  --ink:#2b2b2b;
  --charcoal:#333537;
  --text:#6d6d6d;
  --line:#e2e2e2;
  --page:#f4f4f4;
  --white:#ffffff;
}
*{box-sizing:border-box;margin:0;padding:0}
html,body{width:1200px;height:3336px;overflow:hidden}
body{background:var(--page);font-family:"Open Sans",Arial,sans-serif;color:var(--text);position:relative}
.topbar{height:32px;background:var(--charcoal);display:flex;justify-content:flex-end;align-items:center;gap:10px;padding-right:96px}
.topbar .dot{width:14px;height:14px;border-radius:50%;background:#cfcfcf}
.masthead{background:var(--white);height:136px;text-align:center}
.brand{font-family:"Cinzel",Georgia,serif;font-size:44px;font-weight:400;color:var(--ink);padding-top:18px;letter-spacing:1px}
.nav{display:flex;justify-content:center;margin-top:14px}
.nav a{font-size:15px;text-transform:uppercase;color:var(--ink);text-decoration:none;padding:4px 28px 10px;letter-spacing:1px;border-right:1px solid var(--line)}
.nav a:last-child{border-right:none}
.nav a.active{color:var(--green);box-shadow:inset 0 -3px 0 var(--green)}
.hero{position:relative;height:400px;background:radial-gradient(ellipse at 55% 50%,#ffe2a6 0%,#f08a3a 18%,#b9332a 45%,#4b1a17 100%)}
.hero-copy{position:absolute;left:88px;top:138px;color:var(--white);font-family:"Cinzel",Georgia,serif;font-weight:700;font-size:32px;line-height:42px;text-shadow:0 2px 6px rgba(0,0,0,.5)}
.hero-arrow{position:absolute;top:190px;width:10px;height:20px;background:rgba(255,255,255,.5)}
.topics{display:flex;height:144px;background:var(--green)}
.topic{flex:1;display:flex;align-items:center;justify-content:center;gap:26px;color:var(--white);font-family:"Cinzel",Georgia,serif;font-size:26px}
.topic.current{background:var(--charcoal);color:var(--green)}
.layout{position:absolute;top:780px;left:88px;width:1032px;display:flex;justify-content:space-between}
.posts{width:640px}
.post{height:468px;margin-bottom:20px;display:flex;gap:24px}
.post-meta{width:72px;text-align:right}
.date-day{background:var(--green);color:var(--white);font-size:36px;height:64px;line-height:64px;text-align:center}
.date-month{font-size:13px;font-weight:700;color:var(--ink);margin-top:10px;line-height:17px}
.meta-label{font-size:11px;font-weight:700;color:var(--ink);margin-top:10px;line-height:14px}
.meta-value{font-size:11px;color:var(--text)}
.share{width:56px;height:56px;background:var(--charcoal);margin:14px 0 0 16px;display:flex;align-items:center;justify-content:center}
.post-card{flex:1;background:var(--white);padding:12px;box-shadow:0 1px 3px rgba(0,0,0,.08)}
.post-photo{height:250px}
.post-title{font-family:"Cinzel",Georgia,serif;font-weight:700;font-size:17px;color:var(--ink);margin-top:20px}
.post-text{font-size:13px;line-height:19px;margin-top:8px}
.post-foot{display:flex;justify-content:space-between;align-items:center;margin-top:18px}
.counts{display:flex;gap:8px}
.count{width:40px;height:30px;border:1px solid var(--line);font-size:10px;text-align:center;line-height:14px;padding-top:1px;color:var(--text)}
.btn{background:var(--green);color:var(--white);font-size:12px;font-weight:700;text-transform:uppercase;padding:7px 12px;border:none}
.sidebar{width:344px}
.widget{background:var(--white);padding:16px 18px;margin-bottom:40px;box-shadow:0 1px 3px rgba(0,0,0,.08)}
.widget-title{font-family:"Cinzel",Georgia,serif;font-size:22px;color:var(--ink);padding-bottom:10px;border-bottom:1px solid var(--line);margin-bottom:14px}
.widget-title span{color:var(--green)}
.about-photo{height:150px}
.widget p{font-size:12px;line-height:17px;margin:12px 0}
.field{height:30px;border:1px solid var(--line);margin-bottom:10px;font-size:11px;padding:7px 10px;color:#aaa}
.tags{display:grid;grid-template-columns:repeat(4,1fr);gap:6px}
.tag{background:var(--green-dark);color:var(--white);font-size:10px;text-transform:uppercase;text-align:center;padding:6px 2px}
.recent{display:flex;gap:10px;margin-bottom:12px}
.recent-date{width:44px;height:30px;background:var(--charcoal);color:var(--green);font-size:11px;font-weight:700;text-align:center;line-height:30px;flex:none}
.recent-text{font-size:11px;line-height:14px}
.recent-text b{color:var(--ink)}
.weather{display:flex;gap:6px}
.wx{flex:1;height:96px;color:var(--white);text-align:center;font-size:22px;font-weight:700;padding-top:14px}
.wx small{display:block;font-size:10px;font-weight:400;margin-bottom:6px}
.archives li{list-style:none;font-size:13px;padding:7px 0;border-bottom:1px solid #f0f0f0}
.ad{height:560px;background:linear-gradient(160deg,#d42a22,#8d0f0f);color:var(--white);text-align:center;display:flex;align-items:flex-end;justify-content:center;padding-bottom:40px;font-family:"Open Sans",Arial,sans-serif;font-weight:700;font-size:24px;line-height:30px}
.load-more{position:absolute;left:88px;top:3212px;width:640px;height:48px;background:var(--green);color:var(--white);text-align:center;line-height:48px;font-weight:700;font-size:15px}
.footer{position:absolute;left:0;bottom:0;width:1200px;height:48px;background:var(--charcoal);color:#bbb;font-size:12px;text-align:center;line-height:48px}
</style>
</head>
<body>
<div class="topbar"><span class="dot"></span><span class="dot"></span><span class="dot"></span><span class="dot"></span></div>
<header class="masthead">
  <div class="brand">Tandem K</div>
  <nav class="nav"><a class="active" href="#">About Me</a><a href="#">Recent Blog</a><a href="#">Reader Comments</a><a href="#">Contact Us</a></nav>
</header>
<section class="hero" role="img" aria-label="Photo of two hands forming a heart against a sunset">
  <span class="hero-arrow" style="left:0"></span><span class="hero-arrow" style="right:0"></span>
  <div class="hero-copy">A Different Kind of Company.<br>A Different Kind of<br>Tandem K</div>
</section>
<section class="topics">
  <div class="topic"><svg width="58" height="62" viewBox="0 0 58 62"><path d="M29 14c-6-6-26-6-26 16 0 18 14 30 26 28 12 2 26-10 26-28 0-22-20-22-26-16z" fill="#fff"/><path d="M29 14c0-6 4-11 10-13" stroke="#fff" stroke-width="3" fill="none"/></svg>Nutrition</div>
  <div class="topic current"><svg width="62" height="62" viewBox="0 0 62 62"><circle cx="31" cy="31" r="27" fill="none" stroke="#8db31e" stroke-width="4"/><path d="M31 18l4 9h9l-7 6 3 10-9-6-9 6 3-10-7-6h9z" fill="#8db31e"/></svg>Exercise</div>
  <div class="topic"><svg width="76" height="54" viewBox="0 0 76 54"><circle cx="16" cy="36" r="14" fill="none" stroke="#fff" stroke-width="4"/><circle cx="60" cy="36" r="14" fill="none" stroke="#fff" stroke-width="4"/><path d="M16 36l14-20h20l10 20M30 16l10 20h-24M48 8h8" stroke="#fff" stroke-width="4" fill="none"/></svg>Sports</div>
</section>

<main class="layout">
  <div class="posts">
    <article class="post">
      <div class="post-meta"><div class="date-day">02</div><div class="date-month">JULY<br>2016</div><div class="meta-label">POSTED BY</div><div class="meta-value">Admin</div><div class="meta-label">CATEGORY</div><div class="meta-value">Terms</div>
        <div class="share"><svg width="26" height="26" viewBox="0 0 26 26"><circle cx="6" cy="13" r="4" fill="#fff"/><circle cx="20" cy="5" r="4" fill="#fff"/><circle cx="20" cy="21" r="4" fill="#fff"/><path d="M6 13L20 5M6 13l14 8" stroke="#fff" stroke-width="2"/></svg></div></div>
      <div class="post-card"><div class="post-photo" role="img" aria-label="Photo of three women doing yoga in a bright studio" style="background:linear-gradient(180deg,#e8e4e0,#b9a79a)"></div>
        <h3 class="post-title">Lorem Ipsum Dolor Sit Amet Consectetuer Adipiscing</h3>
        <p class="post-text">Lorem ipsum dolor sit amet, consectetuer adipiscing elit, sed diam nonummy nibh euismod tincidunt ut laoreet dolore magna aliquam erat volutpat. Ut wisi enim ad minim.</p>
        <div class="post-foot"><div class="counts"><span class="count">0<br>like</span><span class="count">0<br>post</span><span class="count">0<br>pin</span><span class="count">0<br>share</span></div><span class="btn">Read More</span></div></div>
    </article>
    <article class="post">
      <div class="post-meta"><div class="date-day">02</div><div class="date-month">JULY<br>2016</div><div class="meta-label">POSTED BY</div><div class="meta-value">Admin</div><div class="meta-label">CATEGORY</div><div class="meta-value">Terms</div>
        <div class="share"><svg width="26" height="26" viewBox="0 0 26 26"><circle cx="6" cy="13" r="4" fill="#fff"/><circle cx="20" cy="5" r="4" fill="#fff"/><circle cx="20" cy="21" r="4" fill="#fff"/><path d="M6 13L20 5M6 13l14 8" stroke="#fff" stroke-width="2"/></svg></div></div>
      <div class="post-card"><div class="post-photo" role="img" aria-label="Photo of a mother and daughter hugging outdoors in green foliage" style="background:linear-gradient(135deg,#4f7a2a,#b7c97a 60%,#e8c9a8)"></div>
        <h3 class="post-title">Lorem Ipsum Dolor Sit Amet Consectetuer Adipiscing</h3>
        <p class="post-text">Lorem ipsum dolor sit amet, consectetuer adipiscing elit, sed diam nonummy nibh euismod tincidunt ut laoreet dolore magna aliquam erat volutpat. Ut wisi enim ad minim.</p>
        <div class="post-foot"><div class="counts"><span class="count">0<br>like</span><span class="count">0<br>post</span><span class="count">0<br>pin</span><span class="count">0<br>share</span></div><span class="btn">Read More</span></div></div>
    </article>
    <article class="post">
      <div class="post-meta"><div class="date-day">02</div><div class="date-month">JULY<br>2016</div><div class="meta-label">POSTED BY</div><div class="meta-value">Admin</div><div class="meta-label">CATEGORY</div><div class="meta-value">Terms</div>
        <div class="share"><svg width="26" height="26" viewBox="0 0 26 26"><circle cx="6" cy="13" r="4" fill="#fff"/><circle cx="20" cy="5" r="4" fill="#fff"/><circle cx="20" cy="21" r="4" fill="#fff"/><path d="M6 13L20 5M6 13l14 8" stroke="#fff" stroke-width="2"/></svg></div></div>
      <div class="post-card"><div class="post-photo" role="img" aria-label="Photo of a woman exercising on a grassy lawn" style="background:linear-gradient(180deg,#cfe0a8,#7fae3a)"></div>
        <h3 class="post-title">Lorem Ipsum Dolor Sit Amet Consectetuer Adipiscing</h3>
        <p class="post-text">Lorem ipsum dolor sit amet, consectetuer adipiscing elit, sed diam nonummy nibh euismod tincidunt ut laoreet dolore magna aliquam erat volutpat. Ut wisi enim ad minim.</p>
        <div class="post-foot"><div class="counts"><span class="count">0<br>like</span><span class="count">0<br>post</span><span class="count">0<br>pin</span><span class="count">0<br>share</span></div><span class="btn">Read More</span></div></div>
    </article>
    <article class="post">
      <div class="post-meta"><div class="date-day">02</div><div class="date-month">JULY<br>2016</div><div class="meta-label">POSTED BY</div><div class="meta-value">Admin</div><div class="meta-label">CATEGORY</div><div class="meta-value">Terms</div>
        <div class="share"><svg width="26" height="26" viewBox="0 0 26 26"><circle cx="6" cy="13" r="4" fill="#fff"/><circle cx="20" cy="5" r="4" fill="#fff"/><circle cx="20" cy="21" r="4" fill="#fff"/><path d="M6 13L20 5M6 13l14 8" stroke="#fff" stroke-width="2"/></svg></div></div>
      <div class="post-card"><div class="post-photo" role="img" aria-label="Photo of a man playing pool at a blue table" style="background:linear-gradient(180deg,#3a3430,#1f5d8a 70%,#164a6e)"></div>
        <h3 class="post-title">Lorem Ipsum Dolor Sit Amet Consectetuer Adipiscing</h3>
        <p class="post-text">Lorem ipsum dolor sit amet, consectetuer adipiscing elit, sed diam nonummy nibh euismod tincidunt ut laoreet dolore magna aliquam erat volutpat. Ut wisi enim ad minim.</p>
        <div class="post-foot"><div class="counts"><span class="count">0<br>like</span><span class="count">0<br>post</span><span class="count">0<br>pin</span><span class="count">0<br>share</span></div><span class="btn">Read More</span></div></div>
    </article>
    <article class="post">
      <div class="post-meta"><div class="date-day">02</div><div class="date-month">JULY<br>2016</div><div class="meta-label">POSTED BY</div><div class="meta-value">Admin</div><div class="meta-label">CATEGORY</div><div class="meta-value">Terms</div>
        <div class="share"><svg width="26" height="26" viewBox="0 0 26 26"><circle cx="6" cy="13" r="4" fill="#fff"/><circle cx="20" cy="5" r="4" fill="#fff"/><circle cx="20" cy="21" r="4" fill="#fff"/><path d="M6 13L20 5M6 13l14 8" stroke="#fff" stroke-width="2"/></svg></div></div>
      <div class="post-card"><div class="post-photo" role="img" aria-label="Photo of a smiling couple by the sea" style="background:linear-gradient(180deg,#8fb4cf,#c98e6a 55%,#6e4a36)"></div>
        <h3 class="post-title">Lorem Ipsum Dolor Sit Amet Consectetuer Adipiscing</h3>
        <p class="post-text">Lorem ipsum dolor sit amet, consectetuer adipiscing elit, sed diam nonummy nibh euismod tincidunt ut laoreet dolore magna aliquam erat volutpat. Ut wisi enim ad minim.</p>
        <div class="post-foot"><div class="counts"><span class="count">0<br>like</span><span class="count">0<br>post</span><span class="count">0<br>pin</span><span class="count">0<br>share</span></div><span class="btn">Read More</span></div></div>
    </article>
  </div>

  <aside class="sidebar">
    <section class="widget">
      <h2 class="widget-title">About <span>Me</span></h2>
      <div class="about-photo" role="img" aria-label="Portrait photo of the blog author in an office" style="background:linear-gradient(135deg,#c9d2d8,#5d6670)"></div>
      <p>Lorem ipsum dolor sit amet, consectetuer adipiscing elit, sed diam nonummy nibh euismod tincidunt ut laoreet dolore magna aliquam erat volutpat. Ut wisi enim ad minim veniam, quis nostrud exerci tation ullamcorper suscipit lobortis nisl ut aliquip ex ea commodo consequat.</p>
      <span class="btn">Read More</span>
    </section>
    <section class="widget">
      <h2 class="widget-title">News Letter <span>Sign Up</span></h2>
      <div class="field">Name</div><div class="field">Email</div><div class="field">Phone</div>
      <div style="text-align:right"><span class="btn">Submit</span></div>
    </section>
    <section class="widget">
      <h2 class="widget-title">Tags</h2>
      <div class="tags"><span class="tag">Europe</span><span class="tag">Australia</span><span class="tag">Canada</span><span class="tag">Asia</span><span class="tag">New Zealand</span><span class="tag">Caribbean</span><span class="tag">USA</span><span class="tag">UK</span><span class="tag">South Pacific</span><span class="tag">Africa</span><span class="tag">Mexico</span><span class="tag">Middle East</span></div>
    </section>
    <section class="widget">
      <h2 class="widget-title">Recent <span>Posts</span></h2>
      <div class="recent"><span class="recent-date">02 JUL</span><div class="recent-text"><b>Lorem ipsum dolor sit amet</b><br>consectetuer adipiscing elit sed diam nonummy.</div></div>
      <div class="recent"><span class="recent-date">02 JUL</span><div class="recent-text"><b>Lorem ipsum dolor sit amet</b><br>consectetuer adipiscing elit sed diam nonummy.</div></div>
      <div class="recent"><span class="recent-date">02 JUL</span><div class="recent-text"><b>Lorem ipsum dolor sit amet</b><br>consectetuer adipiscing elit sed diam nonummy.</div></div>
    </section>
    <section class="widget">
      <h2 class="widget-title">Weather</h2>
      <div class="weather"><div class="wx" style="background:#f39c2f"><small>MON</small>32°</div><div class="wx" style="background:#f3c72f"><small>TUE</small>16°</div><div class="wx" style="background:#3d9bd8"><small>WED</small>10°</div><div class="wx" style="background:#2bb3a3"><small>THU</small>20°</div></div>
    </section>
    <section class="widget">
      <h2 class="widget-title">Archives</h2>
      <ul class="archives"><li>July 2016</li><li>June 2016</li><li>May 2016</li><li>April 2016</li><li>March 2016</li><li>February 2016</li><li>January 2016</li></ul>
    </section>
    <div class="ad" role="img" aria-label="Advertisement photo of a tall stack of red sauce bottles">Sun Ripe Tomatoes,<br>Bottled by Redvale.</div>
  </aside>
</main>

<div class="load-more">⊕ Load More Blogs</div>
<footer class="footer">Copyright © 2016 · Tandem K · All Rights Reserved.</footer>
</body>
</html>
```